Meadowlark Property Review is a leading provider of residential appraisal and home inspection products in S

I need a business card/logo designed that obviously describes my business. We are a residential appraisal and home inspection company in Springfield, MO. We offer residential appraisals, home inspection, pest inspection and radon gas measurement. We have been in business for 18 years and hold state certified residential appraisal licenses and OBREX certified home inspection licenses. I have a logo that I really like and will attach, but would be open to new suggestions. I like more modern designs than traditional and would like a two sided card with our services, licenses and qualifications on the back.

```html
<!DOCTYPE html>
<html lang="en">
<head>
<meta charset="utf-8">
<title>Meadowlark Property Review — Business Card</title>
<link href="https://fonts.googleapis.com/css2?family=Source+Sans+3:ital,wght@0,400;0,600;1,400&display=swap" rel="stylesheet">
<style>
  :root {
    --stage: #2b2b2b;
    --paper: #ffffff;
    --gold: #a07d45;
    --gold-light: #ad8b55;
    --orange: #f6a21d;
    --ink: #6b6055;
    --ink-soft: #8a8178;
    --rule: #c9c4bd;
    --white: #ffffff;
    --white-soft: rgba(255,255,255,.55);
  }
  * { box-sizing: border-box; margin: 0; padding: 0; }
  html, body { width: 1200px; height: 659px; overflow: hidden; }
  body {
    background: var(--stage);
    font-family: "Source Sans 3", "Helvetica Neue", Arial, sans-serif;
    position: relative;
  }
  .card {
    position: absolute;
    top: 192px;
    width: 480px;
    height: 274px;
    overflow: hidden;
  }

  /* Front */
  .card--front { left: 100px; background: var(--paper); border-bottom: 5px solid var(--orange); }
  .brand {
    position: absolute; left: 34px; top: 36px;
    display: flex; align-items: center; gap: 10px;
  }
  .brand__dot { width: 14px; height: 14px; border-radius: 50%; background: var(--orange); }
  .brand__name { font-size: 21px; font-weight: 600; color: var(--gold); line-height: 1.1; }
  .address {
    position: absolute; right: 34px; top: 90px; text-align: right;
    font-style: normal; font-size: 12.5px; line-height: 1.45; color: var(--ink);
  }
  .address__web { color: var(--orange); }
  .divider {
    position: absolute; left: 178px; right: 34px; top: 152px;
    height: 1px; background: var(--rule);
  }
  .person { position: absolute; left: 34px; top: 160px; }
  .person__name { font-size: 19px; font-weight: 600; color: var(--ink-soft); line-height: 1.1; }
  .person__title { font-size: 13px; color: var(--orange); margin-bottom: 6px; }
  .contact { list-style: none; font-size: 12.5px; color: var(--ink); line-height: 1.5; }
  .contact li { display: flex; align-items: center; gap: 8px; }
  .contact svg { width: 11px; height: 11px; fill: var(--ink); flex: none; }

  /* Back */
  .card--back {
    left: 620px;
    background: linear-gradient(120deg, var(--gold) 0%, var(--gold-light) 55%, var(--gold) 100%);
  }
  .back-brand {
    position: absolute; right: 40px; top: 40px;
    display: flex; align-items: center; gap: 12px;
  }
  .back-brand__dot { width: 22px; height: 22px; border-radius: 50%; background: var(--orange); }
  .back-brand__name { font-size: 22px; font-weight: 600; color: var(--white); }
  .back-info {
    position: absolute; left: 38px; right: 40px; bottom: 34px;
    display: flex; justify-content: space-between; align-items: flex-end; gap: 20px;
  }
  .services, .credentials {
    list-style: none; font-size: 13px; font-style: italic; line-height: 1.5; color: var(--white);
  }
  .credentials {
    text-align: right; padding-left: 20px; border-left: 1px solid var(--white-soft);
  }
  .credentials__years { font-style: normal; font-weight: 600; color: var(--white); }
</style>
</head>
<body>
  <section class="card card--front" aria-label="Business card front">
    <div class="brand">
      <span class="brand__dot"></span>
      <span class="brand__name">Meadowlark Property Review</span>
    </div>
    <address class="address">
      2140 Larkspur Avenue<br>
      Springfield, Missouri 65804<br>
      <span class="address__web">www.meadowlarkreview.com</span>
    </address>
    <div class="divider"></div>
    <div class="person">
      <p class="person__name">Dana Whitfield</p>
      <p class="person__title">CEO/Founder</p>
      <ul class="contact">
        <li><svg viewBox="0 0 12 12"><path d="M2.5 0.5l2 2.3-1.2 1.5c.8 1.7 2 2.9 3.7 3.7l1.5-1.2 2.3 2-1.1 2.2C5.3 10.8 1.2 6.7.3 1.6z"/></svg>417 555 0182</li>
        <li><svg viewBox="0 0 12 12"><rect x="1" y="4" width="10" height="6" rx="1"/><rect x="3" y="1" width="6" height="3"/></svg>417 555 0194</li>
        <li><svg viewBox="0 0 12 12"><path d="M0 2h12v8H0z M1 3l5 3.5L11 3" stroke="#fff" stroke-width="0.8"/></svg>dana@meadowlarkreview.com</li>
      </ul>
    </div>
  </section>

  <section class="card card--back" aria-label="Business card back">
    <div class="back-brand">
      <span class="back-brand__dot"></span>
      <span class="back-brand__name">Meadowlark Property Review</span>
    </div>
    <div class="back-info">
      <ul class="services">
        <li>Residential appraisal</li>
        <li>Home inspection</li>
        <li>Pest inspection</li>
        <li>Radon gas measurement.</li>
      </ul>
      <ul class="credentials">
        <li class="credentials__years">18 years in business</li>
        <li>State certified residential appraiser</li>
        <li>OBREX certified home inspector</li>
      </ul>
    </div>
  </section>
</body>
</html>
```